Verlindo Magician

I want the business card for my business to give to people who watch that later I will be employed to show magic here is my website http://www.verlindoillusions.example/I want the interesting design , i am very opened for formal and informal, I watch a lot of design so don't stick to the common shape and form but i hope it can also be produced the thing to write on will be the same as in picture that i will upload , i also will upload the logo for you that so can be easy to useDenis CostilleMagicianMAGICIAN BALSAMO 17 rue des Tilleuls - 25000 BESANÇON contact@verlindoillusions.example tel. 0381 946 157 tel. 0674 219 503

```html
<!DOCTYPE html>
<html lang="fr">
<head>
<meta charset="utf-8">
<title>Verlindo Magician – Business Card</title>
<link rel="stylesheet" href="https://fonts.googleapis.com/css2?family=Jost:wght@300;400&display=swap">
<style>
  :root {
    --backdrop: #202020;
    --paper: #f1f1f1;
    --card-dark: #1b1c1d;
    --ink: #111111;
    --accent: #d7191c;
    --light-text: #e6e6e6;
    --rule: #6a6a6a;
    --portrait-tone: #2a2a2a;
  }
  * { box-sizing: border-box; margin: 0; padding: 0; }
  html, body {
    width: 1200px; height: 800px; overflow: hidden;
    background: var(--backdrop);
    font-family: "Jost", "Futura", sans-serif;
  }
  .canvas {
    position: relative; width: 1200px; height: 800px;
  }
  .card {
    position: absolute; left: 350px; width: 500px; height: 290px;
    box-shadow: 0 6px 18px rgba(0,0,0,.45);
  }
  /* Front */
  .card-front {
    top: 90px; background: var(--paper);
    display: flex; flex-direction: column; align-items: center; justify-content: center;
  }
  .portrait {
    width: 130px; height: 160px;
    background: radial-gradient(ellipse at 50% 40%, #3a3a3a 0%, var(--portrait-tone) 70%, #1a1a1a 100%);
    border-radius: 60px 60px 22px 22px;
  }
  .brand-name {
    margin-top: 10px;
    font-weight: 300; font-size: 26px; letter-spacing: 2px;
    text-transform: uppercase; color: var(--ink);
  }
  /* Back */
  .card-back {
    top: 420px; background: var(--card-dark); color: var(--light-text);
  }
  .identity {
    position: absolute; right: 292px; top: 108px; text-align: right;
  }
  .identity .person {
    font-weight: 300; font-size: 22px; color: var(--accent);
    text-transform: uppercase; letter-spacing: .5px; line-height: 1;
  }
  .identity .role {
    font-weight: 300; font-size: 13px; letter-spacing: 1.5px;
    text-transform: uppercase; margin-top: 4px;
  }
  .divider {
    position: absolute; left: 222px; top: 92px; width: 1px; height: 62px;
    background: var(--rule);
  }
  .contact-list {
    position: absolute; left: 236px; top: 88px; list-style: none;
    font-weight: 300; font-size: 12.5px; line-height: 17px;
  }
  .contact-list li { display: flex; align-items: center; gap: 6px; }
  .contact-list svg { width: 10px; height: 10px; fill: var(--accent); flex: none; }
  .address {
    position: absolute; left: 0; right: 0; bottom: 46px; text-align: center;
    font-weight: 300; font-size: 12.5px;
  }
</style>
</head>
<body>
<main class="canvas">
  <section class="card card-front">
    <div class="portrait" role="img" aria-label="Black ink illustration of the magician holding a playing card"></div>
    <p class="brand-name">Verlindo Magicien</p>
  </section>

  <section class="card card-back">
    <div class="identity">
      <p class="person">Marc Ravoulet</p>
      <p class="role">Magician</p>
    </div>
    <div class="divider"></div>
    <ul class="contact-list">
      <li>
        <svg viewBox="0 0 10 10" aria-hidden="true"><path d="M2 0.5 L3.6 0.5 L4.2 2.8 L3 3.6 C3.6 5 5 6.4 6.4 7 L7.2 5.8 L9.5 6.4 L9.5 8 C9.5 9 8.8 9.5 8 9.5 C3.8 9.3 0.7 6.2 0.5 2 C0.5 1.2 1 0.5 2 0.5 Z"/></svg>
        0381 946 157
      </li>
      <li>
        <svg viewBox="0 0 10 10" aria-hidden="true"><path d="M2 0.5 L3.6 0.5 L4.2 2.8 L3 3.6 C3.6 5 5 6.4 6.4 7 L7.2 5.8 L9.5 6.4 L9.5 8 C9.5 9 8.8 9.5 8 9.5 C3.8 9.3 0.7 6.2 0.5 2 C0.5 1.2 1 0.5 2 0.5 Z"/></svg>
        0674 219 503
      </li>
      <li>
        <svg viewBox="0 0 10 10" aria-hidden="true"><path d="M0.5 2 H9.5 V8 H0.5 Z M0.5 2 L5 5.5 L9.5 2" /></svg>
        contact@verlindoillusions.example
      </li>
      <li>
        <svg viewBox="0 0 10 10" aria-hidden="true"><circle cx="5" cy="5" r="4.5"/></svg>
        www.verlindoillusions.example
      </li>
    </ul>
    <p class="address">17 rue des Tilleuls - 25000 BESANÇON</p>
  </section>
</main>
</body>
</html>
```